BRIGHT RIVER POWER.

I'd like my business logo.
contact name: Dennis Halvorsen
phone:0438759164
email: info@brightriverpower.net.au
website: www.brightriverpower.net.au

services:
solar
battery storage
LED lighting
energy saving solutions
general electrical
I'd like the design to look professional

Target Market(s)

Everyone

Industry/Entity Type

Business

Contact Information for Business Card

as described above

Requirements
Must have
• Id like the colours and the design to work well with my logo.

```html
<!DOCTYPE html>
<html lang="en">
<head>
<meta charset="utf-8">
<title>Bright River Power – Business Card</title>
<link href="https://fonts.googleapis.com/css2?family=Source+Sans+3:wght@400;600&display=swap" rel="stylesheet">
<style>
  :root {
    --bg-top: #676767;
    --bg-bottom: #535353;
    --card-light: #ffffff;
    --card-dark: #000000;
    --green: #5cb535;
    --orange: #f5a000;
    --ink: #222222;
    --rule: #d6d6d6;
  }
  * { margin: 0; padding: 0; box-sizing: border-box; }
  html, body { width: 1200px; height: 900px; overflow: hidden; }
  body {
    position: relative;
    background: linear-gradient(180deg, var(--bg-top), var(--bg-bottom));
    font-family: "Source Sans 3", "Myriad Pro", sans-serif;
    color: var(--ink);
  }
  .card {
    position: absolute;
    top: 306px;
    width: 440px;
    height: 271px;
    border-radius: 12px;
    box-shadow: 0 2px 6px rgba(0,0,0,.25);
  }
  .card--front { left: 149px; background: var(--card-light); }
  .card--back { left: 608px; background: var(--card-dark); }

  .brand {
    position: absolute;
    display: flex;
    align-items: center;
    gap: 12px;
    white-space: nowrap;
  }
  .brand__dot {
    width: 26px; height: 26px;
    border-radius: 50%;
    background: var(--orange);
    flex: none;
  }
  .brand__name {
    font-weight: 600;
    font-size: 31px;
    letter-spacing: .5px;
    color: var(--green);
  }
  .card--front .brand { left: 50%; top: 50px; transform: translateX(-50%); }
  .card--back .brand { left: 50%; top: 50%; transform: translate(-50%, -50%); }

  .contact {
    position: absolute;
    right: 231px;
    top: 150px;
    text-align: right;
  }
  .contact__name {
    font-weight: 600;
    font-size: 17px;
    color: var(--green);
    margin-bottom: 13px;
  }
  .contact__line {
    display: flex;
    justify-content: flex-end;
    align-items: center;
    gap: 6px;
    font-size: 12.5px;
    line-height: 16px;
  }
  .contact__line svg { width: 9px; height: 9px; fill: var(--orange); flex: none; }

  .divider {
    position: absolute;
    left: 219px;
    top: 146px;
    bottom: 0;
    width: 1px;
    background: var(--rule);
  }

  .services {
    position: absolute;
    left: 235px;
    top: 152px;
  }
  .services__title {
    font-size: 15px;
    color: var(--green);
    letter-spacing: .3px;
    margin-bottom: 14px;
  }
  .services__list { list-style: none; }
  .services__list li {
    position: relative;
    padding-left: 10px;
    font-size: 12.5px;
    line-height: 16px;
  }
  .services__list li::before {
    content: "";
    position: absolute;
    left: 0; top: 6px;
    width: 5px; height: 5px;
    border-radius: 50%;
    background: var(--orange);
  }
</style>
</head>
<body>
  <section class="card card--front">
    <div class="brand">
      <span class="brand__dot"></span>
      <span class="brand__name">Bright River Power</span>
    </div>

    <div class="contact">
      <p class="contact__name">Dennis Halvorsen</p>
      <p class="contact__line">0438759164
        <svg viewBox="0 0 10 10"><path d="M2 1h2l1 2-1.2 1a6 6 0 0 0 2.2 2.2L7 5l2 1v2l-1 1C4.5 9 1 5.5 1 2z"/></svg>
      </p>
      <p class="contact__line">info@brightriverpower.net.au
        <svg viewBox="0 0 10 10"><path d="M0 2h10v6H0z M0 2l5 3.5L10 2" fill="var(--orange)"/></svg>
      </p>
      <p class="contact__line">www.brightriverpower.net.au
        <svg viewBox="0 0 10 10"><path d="M6 1l3 3-4 4-1-1 3-3-2-2zM4 9L1 6l4-4 1 1-3 3 2 2z"/></svg>
      </p>
    </div>

    <div class="divider"></div>

    <div class="services">
      <h2 class="services__title">WHAT I DO</h2>
      <ul class="services__list">
        <li>Solar</li>
        <li>Battery Storage</li>
        <li>LED Lighting</li>
        <li>Energy Saving Solutions</li>
      </ul>
    </div>
  </section>

  <section class="card card--back">
    <div class="brand">
      <span class="brand__dot"></span>
      <span class="brand__name">Bright River Power</span>
    </div>
  </section>
</body>
</html>
```